Craft Brewery Beer Can Label in Alaska

Design a 16oz can label for a craft brewery.

We are making a can design that can be used for our 6 normal beers. Our desire is to have a standard design but one major element have the color change on each beer type. We included examples of how this works for others.

Elements we general like in designs - mountain scenes, waterfalls, topo map lines, hops. None/all are not required in a design but gives starting options. We are on the ocean in a glacier fjord so think mountains, glaciers and water.

Requirements
Must have
• Company Logo – provided
Bellvane Seal Logo – provided
Saltmoor Brewers Logo – provided

Alcohol warning text -

GOVERNMENT WARNING: (1) According to the Surgeon General, women should not drink alcoholic beverages during pregnancy because of the risk of birth defects. (2) Consumption of alcoholic beverages impairs your ability to drive a car or operate machinery, and may cause health problems.

Beer Name – Gullrock Pilsner
ABV – 4.9% ABV
Size – 16 FL OZ
Nice to have
• Elements we general like in designs - mountain scenes, waterfalls, topo map lines, hops. None/all are not required in a design but gives starting options. We are on the ocean in a glacier fjord so think mountains, glaciers and water.

```html
<!DOCTYPE html>
<html lang="en">
<head>
<meta charset="utf-8">
<title>Gullrock Pilsner – Can Label</title>
<link rel="stylesheet" href="https://fonts.googleapis.com/css2?family=Bebas+Neue&family=Montserrat:wght@500;700;800&family=Roboto+Condensed:wght@700&display=swap">
<style>
  :root {
    --page: #f2f2f2;
    --sky: #2edbff;
    --ink: #0d3a44;
    --title: #f4f6f6;
    --tag: #0b2a31;
    --ridge-light: #52c3d6;
    --ridge: #3a8899;
    --slope: #2a6474;
    --deep: #1c4451;
    --shore: #122a31;
    --night: #040809;
    --badge: #3a3a3a;
  }
  html, body {
    margin: 0;
    padding: 0;
    width: 994px;
    height: 1200px;
    overflow: hidden;
    background: var(--page);
  }
  .label {
    position: absolute;
    left: 32px;
    top: 348px;
    width: 930px;
    height: 504px;
    background: var(--sky);
    overflow: hidden;
    box-shadow: 0 2px 6px rgba(0,0,0,0.18);
  }
  .scenery {
    position: absolute;
    left: 0;
    top: 250px;
    width: 930px;
    height: 254px;
    background:
      radial-gradient(ellipse 38% 60% at 30% 38%, rgba(42,100,116,0.55) 0%, rgba(42,100,116,0) 100%),
      radial-gradient(ellipse 30% 45% at 82% 42%, rgba(28,68,81,0.5) 0%, rgba(28,68,81,0) 100%),
      linear-gradient(180deg,
        rgba(46,219,255,0) 0%,
        var(--ridge-light) 12%,
        var(--ridge) 28%,
        var(--slope) 46%,
        var(--deep) 62%,
        var(--shore) 78%,
        var(--night) 100%);
  }
  .brand {
    position: absolute;
    text-align: center;
    color: var(--ink);
    font-family: "Montserrat", sans-serif;
    font-weight: 800;
    line-height: 1;
  }
  .brand-dot {
    display: block;
    margin: 0 auto 8px;
    border-radius: 50%;
    background: var(--ink);
  }
  .brand-name { display: block; }
  .brand-sub { display: block; }
  .brand--main { width: 140px; top: 51px; }
  .brand--main .brand-dot { width: 58px; height: 58px; }
  .brand--main .brand-name { font-size: 26px; letter-spacing: 1px; }
  .brand--main .brand-sub { font-size: 9px; letter-spacing: 7px; margin-top: 4px; padding-left: 7px; }
  .brand--left { left: 146px; }
  .brand--right { left: 616px; }
  .brand--center { left: 403px; top: 83px; width: 100px; }
  .brand--center .brand-dot { width: 40px; height: 40px; margin-bottom: 6px; }
  .brand--center .brand-name { font-size: 18px; letter-spacing: 0.5px; }
  .brand--center .brand-sub { font-size: 6px; letter-spacing: 5px; margin-top: 3px; padding-left: 5px; }

  .beer-name {
    position: absolute;
    color: var(--title);
    font-family: "Bebas Neue", sans-serif;
    line-height: 0.86;
    text-align: center;
    margin: 0;
    font-weight: 400;
  }
  .beer-name span { display: block; white-space: nowrap; }
  .beer-name .line-1 { font-size: 52px; letter-spacing: 2px; }
  .beer-name .line-2 { font-size: 72px; letter-spacing: 2.5px; }
  .beer-name--left { left: 106px; top: 178px; width: 220px; }
  .beer-name--right { left: 579px; top: 178px; width: 220px; }
  .beer-name--vertical {
    left: 397px;
    top: 380px;
    width: 200px;
    height: 92px;
    transform-origin: 0 0;
    transform: rotate(-90deg);
    text-align: left;
  }
  .beer-name--vertical .line-1 { font-size: 44px; letter-spacing: 1px; }
  .beer-name--vertical .line-2 { font-size: 60px; letter-spacing: 1.5px; }

  .tagline {
    position: absolute;
    display: flex;
    align-items: center;
    gap: 6px;
    color: var(--tag);
    font-family: "Montserrat", sans-serif;
    font-weight: 500;
    font-size: 7.5px;
    letter-spacing: 5px;
    white-space: nowrap;
  }
  .tagline::before, .tagline::after {
    content: "";
    flex: 1;
    height: 1.5px;
    background: var(--tag);
  }
  .tagline--left { left: 114px; top: 291px; width: 204px; }
  .tagline--right { left: 587px; top: 291px; width: 207px; }
  .tagline--vertical {
    left: 497px;
    top: 378px;
    width: 198px;
    transform-origin: 0 0;
    transform: rotate(-90deg);
  }

  .volume {
    position: absolute;
    top: 436px;
    width: 140px;
    text-align: center;
    color: #d8f4f8;
    font-family: "Montserrat", sans-serif;
    font-weight: 500;
    font-size: 8px;
    letter-spacing: 0.3px;
  }
  .volume--left { left: 140px; }
  .volume--right { left: 610px; }

  .warning {
    position: absolute;
    margin: 0;
    height: 30px;
    transform-origin: 0 0;
    transform: rotate(-90deg);
    color: #000;
    font-family: "Roboto Condensed", sans-serif;
    font-weight: 700;
    font-size: 7px;
    line-height: 9.5px;
  }
  .warning--left { left: 31px; top: 330px; width: 264px; }
  .warning--right { left: 852px; top: 316px; width: 244px; }

  .badge {
    position: absolute;
    background: var(--badge);
  }
  .badge--origin {
    left: 24px; top: 366px; width: 49px; height: 57px;
    border: 2px solid #fff;
    box-sizing: border-box;
    background: #111;
  }
  .badge--guild {
    left: 841px; top: 331px; width: 60px; height: 98px;
  }
</style>
</head>
<body>
  <main class="label" aria-label="Gullrock Pilsner can label">
    <div class="scenery" role="img" aria-label="Layered glacier mountain range above a calm fjord waterline, teal peaks fading to dark water"></div>

    <p class="warning warning--left">GOVERNMENT WARNING: (1) According to the Surgeon General, women should not drink alcoholic beverages during pregnancy because of the risk of birth defects.</p>

    <div class="brand brand--main brand--left">
      <span class="brand-dot"></span>
      <span class="brand-name">KELDAR</span>
      <span class="brand-sub">BREWING</span>
    </div>
    <h1 class="beer-name beer-name--left"><span class="line-1">GULLROCK</span><span class="line-2">PILSNER</span></h1>
    <div class="tagline tagline--left">CRAFT BREWERY</div>
    <div class="volume volume--left">4.9% ABV&nbsp; | &nbsp;16 FL OZ</div>

    <div class="brand brand--center">
      <span class="brand-dot"></span>
      <span class="brand-name">KELDAR</span>
      <span class="brand-sub">BREWING</span>
    </div>
    <h2 class="beer-name beer-name--vertical"><span class="line-1">GULLROCK</span><span class="line-2">PILSNER</span></h2>
    <div class="tagline tagline--vertical">CRAFT BREWERY</div>

    <div class="brand brand--main brand--right">
      <span class="brand-dot"></span>
      <span class="brand-name">KELDAR</span>
      <span class="brand-sub">BREWING</span>
    </div>
    <h2 class="beer-name beer-name--right"><span class="line-1">GULLROCK</span><span class="line-2">PILSNER</span></h2>
    <div class="tagline tagline--right">CRAFT BREWERY</div>
    <div class="volume volume--right">4.9% ABV&nbsp; | &nbsp;16 FL OZ</div>

    <p class="warning warning--right">GOVERNMENT WARNING: Consumption of alcoholic beverages impairs your ability to drive a car or operate machinery, and may cause health problems.</p>

    <div class="badge badge--origin" role="img" aria-label="Bellvane Seal badge"></div>
    <div class="badge badge--guild" role="img" aria-label="Saltmoor Brewers certification badge"></div>
  </main>
</body>
</html>
```